Redesign 2016 Digital Marketing Website and Convert to Wordpress

Technology needed to integrate:

- redesign and convert to wordpress
- gravity forms
- malware and hacker defense / honeypot (must be very secure from hackers)
- I want gravity forms to be a flow that asks many questions with icons and progress bar.
- 1 home page design
- 1 blog design
- 1 design for internal page content
- 1 multi step gravity form
I want to focus on SMB's. We are a marketing agency thats been around since 2016.

Site is: tallpine.agency

I am looking to redesign the homepage, blog page and services page. The services page will be a template for all inner pages of the site. All content needs to be moved into the new design.

I want to get ride of the weird video.

I need you to install gravity forms pro model so we can pass utms.

I need the gravity form to be a multi step form with icons.

All "contact us" or "get a free assesments" call to actions will go to this form only.

step 1:
what is your website

step 2:
what industry are you in
- option
- Home Services
- Legal
- Ecommerce
- Lead Gen

No matter which one they select its going to produce a differnt calculator for them.

Law:
How many leads did you get last month
how much is each ase worth on average
How much revenue do you want to make

Home servicse:
How many bookings did you get last month
How much is each service worht on average
How much revenue do you wangt to make

Ecommerce:
What is your average order value
How muny purchases did you have last month
How much revenue did you drive
How much revenue do you want to drive

For lead gen:
How many leads did you get lawt month
How much revenue did they generate

Step 3:
What is your current advertising budget

step 4:
Do you have a CRM and if so what is it

Step 5:
What is your personal informagtion
name
email
phone

Let me know if this is enough to get you going

Small and medium sized law firms, ecommerce, home services and lead gen customers.

We are a digital marketing agency

• Use whats on the current site and improve upon it

• Must be very secure, developed into a wordpress website. using gravity forms. remove my photo and my staffs photo, depersonalize it so it doesnt mention me or sam crolley. Use the same color scheme. I am looking to redesign the homepage, blog page and services page. The services page will be a template for all inner pages of the site. All content needs to be moved into the new design. I want to get ride of the weird video. I need you to install gravity forms pro model so we can pass utms. I need the gravity form to be a multi step form with icons. All "contact us" or "get a free assesments" call to actions will go to this form only. step 1: what is your website step 2: what industry are you in - option - Home Services - Legal - Ecommerce - Lead Gen No matter which one they select its going to produce a differnt calculator for them. Law: How many leads did you get last month how much is each ase worth on average How much revenue do you want to make Home servicse: How many bookings did you get last month How much is each service worht on average How much revenue do you wangt to make Ecommerce: What is your average order value How muny purchases did you have last month How much revenue did you drive How much revenue do you want to drive For lead gen: How many leads did you get lawt month How much revenue did they generate How much revenue do you want to make Step 3: What is your current advertising budget step 4: Do you have a CRM and if so what is it Step 5: What is your personal informagtion name email phone Let me know if this is enough to get you going
• SHOULD NOT BE SLOPPY, I AM LOOKING FOR ATTENTION TO DETAIL.

```html
<!DOCTYPE html>
<html lang="en">
<head>
<meta charset="utf-8">
<title>Tall Pine Growth Marketing – Out of Home Advertising</title>
<link href="https://fonts.googleapis.com/css2?family=Poppins:wght@400;500;600;700;800&display=swap" rel="stylesheet">
<style>
:root{
  --brand:#6e1317;
  --brand-deep:#5a0f12;
  --ink:#2b2b2b;
  --charcoal:#262626;
  --nav:#2a2a2a;
  --text:#3a3a3a;
  --muted:#555;
  --partner:#666;
  --partner-blue:#3b75c9;
  --soft:#f2f2f2;
  --line:#e2e2e2;
  --white:#fff;
}
*{box-sizing:border-box;margin:0;padding:0}
html,body{width:1200px;height:3212px;overflow:hidden}
body{font-family:'Poppins',sans-serif;color:var(--text);background:var(--white)}
a{color:inherit;text-decoration:none}
.wrap{width:1050px;margin:0 auto;position:relative}

/* header */
.site-header{height:90px;display:flex;align-items:center}
.site-header .wrap{display:flex;align-items:center;justify-content:space-between}
.brand{display:flex;align-items:center;gap:14px}
.brand-mark{width:60px;height:60px;border-radius:50%;background:var(--brand)}
.brand-name{display:block;font-size:26px;font-weight:400;letter-spacing:2px;color:#5a5a5a;line-height:1}
.brand-tag{display:block;font-size:10px;letter-spacing:5px;color:#777;margin-top:6px}
.header-cta{display:flex;align-items:center;gap:20px}
.call{font-size:17px;font-weight:600;color:#555}
.call strong{color:var(--brand);font-weight:700}
.btn-consult{background:var(--brand);color:#fff;font-weight:600;font-size:16px;padding:13px 13px;border-radius:2px}

.main-nav{height:55px;background:var(--nav);display:flex;justify-content:center;align-items:center;gap:46px}
.main-nav a{color:#fff;font-size:14px;letter-spacing:.3px}

/* hero */
.ooh{height:560px;padding-top:63px}
.ooh .wrap{display:flex;gap:28px}
.ooh-media{position:relative;width:513px;height:432px;flex:none}
.ooh-dots{position:absolute;left:-15px;top:-17px;width:170px;height:200px;
  background-image:radial-gradient(#9a9a9a 1.3px,transparent 1.6px);background-size:13px 13px;
  -webkit-mask:linear-gradient(#000,#000) top/100% 8px no-repeat,linear-gradient(#000,#000) left/8px 100% no-repeat;
          mask:linear-gradient(#000,#000) top/100% 8px no-repeat,linear-gradient(#000,#000) left/8px 100% no-repeat}
.ooh-photo{position:absolute;inset:0;border-radius:12px;
  background:linear-gradient(180deg,#4d7fb3 0%,#87a9cb 45%,#b9c7d3 62%,#4c5a52 75%,#8c949a 100%)}
.ooh-copy{width:509px}
.ooh-copy h1{font-size:36px;font-weight:800;line-height:1.1;color:var(--ink);letter-spacing:.3px;margin-bottom:20px}
.ooh-copy p{font-size:13.8px;line-height:24px;color:var(--text)}
.ooh-copy p+p{margin-top:11px}

/* split */
.split{height:358px;display:flex}
.split-col{padding:72px 40px 0 77px;color:#fff}
.split-col.red{width:603px;background:var(--brand)}
.split-col.dark{flex:1;background:var(--charcoal);padding-left:18px;padding-right:75px}
.split-col h2{font-size:32px;font-weight:500;line-height:40px;letter-spacing:.5px;margin-bottom:20px}
.split-col p{font-size:13.2px;line-height:24px}

/* section titles */
.section-title{text-align:center;font-size:36px;font-weight:800;color:var(--ink);letter-spacing:.5px}
.section-title::after{content:"";display:block;width:94px;height:3px;background:var(--brand);margin:18px auto 0}

/* partners */
.partners{height:362px;background:var(--soft);padding-top:65px}
.partners-intro{text-align:center;font-size:13.5px;line-height:24px;margin-top:26px;color:var(--text)}
.partners-row{position:relative;display:flex;justify-content:space-between;align-items:center;padding:0 10px;margin-top:42px;height:50px}
.partner{font-size:20px;font-weight:500;color:var(--partner)}
.partner.blue{color:var(--partner-blue)}
.chev{position:absolute;top:50%;width:14px;height:14px;margin-top:-7px}
.chev.l{left:-21px}.chev.r{right:-21px}

/* blog */
.blog{height:605px;padding-top:55px}
.posts{position:relative;display:flex;gap:32px;margin-top:42px}
.post{width:329px}
.post-img{height:245px}
.post h3{font-size:18.5px;font-weight:600;line-height:31px;color:var(--ink);margin-top:16px;padding-right:6px}
.posts .chev{top:122px}

/* contact */
.contact{height:547px;background:linear-gradient(180deg,#7a1418 0%,#6a1115 45%,#5d0f12 100%);padding-top:52px}
.contact .section-title{color:#fff}
.contact .section-title::after{background:#fff}
.contact-form{width:862px;margin:42px auto 0;display:grid;grid-template-columns:423px 423px;gap:17px 16px}
.field{background:#fff;height:56px;padding:18px 13px;font-size:13px;font-weight:500;color:#333}
.field.message{grid-column:1 / -1;height:116px;padding-top:16px}
.submit{grid-column:1 / -1;justify-self:center;width:272px;height:56px;border:2px solid #fff;color:#fff;
  font-weight:700;font-size:17px;letter-spacing:.5px;display:flex;align-items:center;justify-content:center;margin-top:-4px}

/* footer */
.footer-top{height:168px;border-bottom:1px solid var(--line)}
.footer-top .wrap{display:flex;align-items:center;height:100%}
.partner-badge{margin-left:98px;display:flex;align-items:center;gap:14px}
.badge-strip{width:24px;height:88px;background:#c62d2d}
.badge-block{width:160px;height:70px;background:#e9eef6;border-radius:4px}
.badge-circle{width:88px;height:88px;border-radius:50%;background:#1d3b63;border:4px solid #cfd8e6;margin-left:66px}
.follow{margin-left:auto;width:242px}
.follow h4{font-size:18px;font-weight:500;letter-spacing:1px;color:#444}
.socials{display:flex;justify-content:space-between;margin-top:16px}
.socials span{width:28px;height:28px;border-radius:50%;background:#3a3a3a}

.footer-links{height:392px;border-bottom:1px solid var(--line);padding-top:40px}
.footer-links .wrap{display:grid;grid-template-columns:243px 297px 268px 1fr}
.footer-links h5{font-size:24px;font-weight:700;color:#3c3c3c;letter-spacing:.3px;margin-bottom:8px}
.footer-links li{list-style:none;font-size:13.5px;line-height:20px;color:#555;margin-bottom:13px}
.guides li{padding-right:10px;line-height:21.5px;margin-bottom:11px}

.copyright{height:75px;display:flex;align-items:center;justify-content:center;font-size:13.5px;color:#555}
</style>
</head>
<body>

<header class="site-header">
  <div class="wrap">
    <a class="brand" href="#">
      <span class="brand-mark"></span>
      <span>
        <span class="brand-name">TALL PINE</span>
        <span class="brand-tag">GROWTH MARKETING</span>
      </span>
    </a>
    <div class="header-cta">
      <span class="call">OR CALL US NOW : <strong>(480) 555-0142</strong></span>
      <a class="btn-consult" href="#">GET A FREE CONSULTATION</a>
    </div>
  </div>
</header>

<nav class="main-nav">
  <a href="#">HOME</a><a href="#">ABOUT</a><a href="#">INDUSTRIES</a><a href="#">SERVICES</a>
  <a href="#">RESOURCES</a><a href="#">TRAINING</a><a href="#">BLOG</a><a href="#">CONTACT US</a>
</nav>

<section class="ooh">
  <div class="wrap">
    <div class="ooh-media">
      <div class="ooh-dots"></div>
      <div class="ooh-photo" role="img" aria-label="Roadside billboard advertising travel under a blue sky beside a highway"></div>
    </div>
    <div class="ooh-copy">
      <h1>OUT OF<br>HOME ADVERTISING</h1>
      <p>Out of home advertising is powerful and can reach massive amounts of people multiple times which reinforces your brand and message. Think of some of the billboards you see when you commute around town. Out of home advertisers come top of mind to consumers when they are in need of their services. If you have an event, a new product, a service or cause, out of home advertising can drive website clicks, phone calls and foot traffic can give you an incredible reach among your local demographics.</p>
      <p>What is the right OOH mix from?&nbsp; After a comprehensive client needs analysis we will create a OOH media strategy that could contain some or all of the following; bus stop ads, billboards, Vehicle wraps, mobile billboards and even Arial advertising. Our rates are competitive and our creative is innovative, effective and designed to invoke emotion from your target audience.</p>
    </div>
  </div>
</section>

<section class="split">
  <div class="split-col red">
    <h2>What is Out of Home (OOH) Advertising?</h2>
    <p>OOH or Out-Of-Home Advertising consists of all advertising you may see outside of your home. For example, billboards, bus stop, arial ads, street teams and mobile billboards are all great examples of OOH Advertising. Out of home advertising is great for mass exposure and drives tons of awareness for your product, promotion, event, sale or cause.</p>
  </div>
  <div class="split-col dark">
    <h2>How Can Out of Home Advertising Help My Business?</h2>
    <p>When you are looking to reach a broad audience then OOH advertising is a solid and highly sought after tactic. When OOH is combined with a digital marketing campaign we can track the effectiveness of an out of home campaign which brings your business better results.</p>
  </div>
</section>

<section class="partners">
  <div class="wrap">
    <h2 class="section-title">STRATEGIC PARTNERS</h2>
    <p class="partners-intro">Our trusted partners provide technical expertise and resources to capture,<br>produce and deliver our traditional media.</p>
    <div class="partners-row">
      <svg class="chev l" viewBox="0 0 14 14"><path d="M9 1 3 7l6 6" fill="none" stroke="#333" stroke-width="1.6"/></svg>
      <span class="partner">Searchly Ads</span>
      <span class="partner">Quest Ads</span>
      <span class="partner blue">Metricsy</span>
      <span class="partner blue">RetargetHub</span>
      <span class="partner">Friendwall</span>
      <span class="partner blue">Webcraft Weekly</span>
      <svg class="chev r" viewBox="0 0 14 14"><path d="M5 1l6 6-6 6" fill="none" stroke="#333" stroke-width="1.6"/></svg>
    </div>
  </div>
</section>

<section class="blog">
  <div class="wrap">
    <h2 class="section-title">LATEST BLOG POSTS</h2>
    <div class="posts">
      <svg class="chev l" viewBox="0 0 14 14"><path d="M9 1 3 7l6 6" fill="none" stroke="#333" stroke-width="1.6"/></svg>
      <article class="post">
        <div class="post-img" role="img" aria-label="Laptop showing a pay-per-click illustration on a wooden desk with a calculator" style="background:linear-gradient(160deg,#6e6a66,#a89c8c 55%,#c9bfb2)"></div>
        <h3>Rankwell Recognizes Tall Pine as One of the Best PPC Companies in Arizona..</h3>
      </article>
      <article class="post">
        <div class="post-img" role="img" aria-label="Desktop, tablet and phone displaying an online store" style="background:linear-gradient(180deg,#d9d6d2,#b9b4ae 60%,#8c8781)"></div>
        <h3>How to Improve E-Commerce Landing Pages with Paid Ads Data</h3>
      </article>
      <article class="post">
        <div class="post-img" role="img" aria-label="Hands holding a tablet showing website traffic analytics" style="background:linear-gradient(160deg,#7b8a8e,#b8bcbb 50%,#9a8f84)"></div>
        <h3>The Best Way to Track Your Keyword Rankings in 2021</h3>
      </article>
      <svg class="chev r" viewBox="0 0 14 14"><path d="M5 1l6 6-6 6" fill="none" stroke="#333" stroke-width="1.6"/></svg>
    </div>
  </div>
</section>

<section class="contact">
  <h2 class="section-title">ELEVATE YOUR MARKETING</h2>
  <form class="contact-form">
    <div class="field">Name</div>
    <div class="field">Email Address</div>
    <div class="field">Phone No</div>
    <div class="field">Subject</div>
    <div class="field message">Message</div>
    <div class="submit">SUBMIT</div>
  </form>
</section>

<footer>
  <div class="footer-top">
    <div class="wrap">
      <a class="brand" href="#">
        <span class="brand-mark"></span>
        <span>
          <span class="brand-name">TALL PINE</span>
          <span class="brand-tag">GROWTH MARKETING</span>
        </span>
      </a>
      <div class="partner-badge" role="img" aria-label="Certified partner badge">
        <span class="badge-strip"></span>
        <span class="badge-block"></span>
      </div>
      <span class="badge-circle" role="img" aria-label="Review listing badge"></span>
      <div class="follow">
        <h4>FOLLOW US</h4>
        <div class="socials">
          <span aria-label="Social link"></span><span aria-label="Social link"></span><span aria-label="Social link"></span><span aria-label="Social link"></span><span aria-label="Social link"></span>
        </div>
      </div>
    </div>
  </div>

  <div class="footer-links">
    <div class="wrap">
      <div>
        <h5>QUICK LINKS</h5>
        <ul><li>About</li><li>Industries</li><li>Services</li><li>Resources</li><li>Training</li><li>Blog</li><li>Contact Us</li></ul>
      </div>
      <div>
        <h5>SERVICES</h5>
        <ul><li>Programmatic Advertising</li><li>Search Engine Marketing (SEM)</li><li>Search Engine Optimization (SEO)</li><li>Content Marketing</li><li>Email Marketing</li><li>Paid Search Advertising</li><li>Paid Social Advertising</li></ul>
      </div>
      <div>
        <h5>INDUSTRIES</h5>
        <ul><li>Ecommerce</li><li>Electricians</li><li>Financial Services Marketing</li><li>Home Builders</li><li>Home Services</li><li>Hvac Companies</li><li>Cosmetic Surgery Centers</li><li>Dental Marketing</li></ul>
      </div>
      <div class="guides">
        <h5>GUIDES</h5>
        <ul><li>Ultimate Guide On Growing Your Medical Practice Business</li><li>Legal Marketing Strategy Guide For Law Firm Offices</li><li>Ultimate Flashpost Ads Guide To Skyrocket Your Leads And Sales</li><li>Ultimate Guide To Search Engine Queries</li></ul>
      </div>
    </div>
  </div>

  <div class="copyright">Copyright © 2024 CompanyName&nbsp; All Rights Reserved. Privacy Policy, Terms Of Use, Press &amp; Media, Cookie Policy</div>
</footer>

</body>
</html>
```